Advertisement Design Project

I would like to have some advertisement ideas to promote my business. Our company provides credit repair, tax preparation, notary service, ledger preparation (for small businesses and independent contractors) tax restoration (help people with liens, levy, garnishments, etc. by negotiating with the NTB in these matters)

The name of our company is Vel Marin Financing
Our "BrivoMendup" program focuses on tax preparation, restoration, and credit repair.
Our "Brisk Start" program prepares ledgers for small business and independent contractors by preparing monthly ledgers so that at tax season they are not having to look everywhere for their receipts in order to get all deductions due to them during the tax season.

We need something that is catchy and will gain attention

attached is our logo. Our slogan is "Happiness, Restored!"

Thank you!

Target Market(s)

The financially distressed
Small business owners
Independent contractors
businesses that rely on credit worthy clients to do business with

Industry/Entity Type

Small Business

Requirements
Must have
• great pictures
nice layout

```html
<!DOCTYPE html>
<html lang="en">
<head>
<meta charset="utf-8">
<title>Vel Marin Financing – BrivoMendup Program</title>
<link rel="stylesheet" href="https://fonts.googleapis.com/css2?family=Arimo:wght@400;700&family=Roboto+Condensed:wght@400;700&family=Cinzel:wght@400&family=Libre+Baskerville&display=swap">
<style>
  :root{
    --ink:#111111;
    --navy:#123c64;
    --navy-deep:#0d2f52;
    --sky:#4f86c2;
    --orange:#f6a21d;
    --orange-deep:#e9851a;
    --violet:#3a3f9e;
    --text:#2a2a2a;
    --paper:#ffffff;
    --soft:#eef0f2;
  }
  *{margin:0;padding:0;box-sizing:border-box}
  html,body{width:953px;height:1200px;overflow:hidden;background:var(--paper)}
  .flyer{position:relative;width:953px;height:1200px;background:var(--paper);font-family:"Arimo",Arial,sans-serif;color:var(--text)}
  .header{position:absolute;left:0;top:0;width:953px;height:330px}
  .header svg{position:absolute;inset:0}
  .header-kicker{position:absolute;left:68px;top:42px;font-family:"Arimo",Arial,sans-serif;font-weight:700;font-size:46px;letter-spacing:3px;color:var(--orange)}
  .header-title{position:absolute;left:68px;top:104px;font-family:"Arimo",Arial,sans-serif;font-weight:700;font-size:56px;color:#e6e6e6;letter-spacing:.5px}
  .intro{position:absolute;left:62px;top:312px;width:494px;font-size:11.6px;line-height:15.6px;text-align:justify;color:var(--text)}
  .program-name{position:absolute;left:58px;top:610px;font-family:"Arimo",Arial,sans-serif;font-size:62px;font-weight:400;color:var(--navy);letter-spacing:-1px}
  .brand-box{position:absolute;left:597px;top:276px;width:258px;height:260px;background:var(--navy-deep);outline:3px solid #c9d3dd;outline-offset:-9px;border:1px solid #b9c3cd;display:flex;flex-direction:column;align-items:center;justify-content:flex-end;padding-bottom:58px}
  .brand-mark{width:44px;height:44px;border:2px solid #ffffff;margin-bottom:40px}
  .brand-name{font-family:"Libre Baskerville",Georgia,serif;font-size:19px;color:#ffffff}
  .slogan{position:absolute;left:597px;top:556px;width:258px;text-align:center;font-family:"Cinzel",Georgia,serif;font-size:40px;line-height:42px;color:#2b2b2b;letter-spacing:1px}
  .provide-tab{position:absolute;left:569px;top:703px;width:384px;height:56px;background:var(--navy);border-radius:28px 0 0 28px;border-top:5px solid var(--sky);color:#ffffff;font-family:"Roboto Condensed",Arial,sans-serif;font-size:32px;letter-spacing:3px;display:flex;align-items:center;padding-left:44px}
  .services{position:absolute;right:101px;top:784px;list-style:none;text-align:right}
  .services li{font-family:"Roboto Condensed",Arial,sans-serif;font-weight:700;font-size:27px;line-height:44px;color:#1b1b1b;display:flex;justify-content:flex-end;align-items:center;gap:10px}
  .services svg{width:28px;height:28px}
  .photo{position:absolute;left:6px;top:720px;width:564px;height:390px;background:radial-gradient(ellipse at 30% 35%,#6f8f3c 0%,#8fa860 30%,#e4cfb4 58%,#f4ede4 75%,#ffffff 95%)}
  .address{position:absolute;right:101px;top:1040px;text-align:right;font-size:14px;line-height:19px;color:#222}
  .browse{position:absolute;left:94px;top:1096px;font-family:"Roboto Condensed",Arial,sans-serif;font-weight:700;font-size:15px;color:#111}
  .footer{position:absolute;left:0;top:1120px;width:953px;height:80px}
  .footer svg{position:absolute;inset:0}
  .footer-web{position:absolute;left:40px;top:22px;font-family:"Arimo",Arial,sans-serif;font-weight:700;font-size:27px;letter-spacing:2px;color:#ffffff}
  .footer-call{position:absolute;right:36px;top:22px;font-family:"Arimo",Arial,sans-serif;color:#ffffff;font-size:20px;letter-spacing:1px}
  .footer-call strong{font-size:30px;letter-spacing:.5px}
</style>
</head>
<body>
<main class="flyer">
  <header class="header">
    <svg width="953" height="330" viewBox="0 0 953 330" aria-hidden="true">
      <path d="M0 0H953V250C820 300 640 300 420 280C250 265 100 252 0 278Z" fill="var(--ink)"/>
      <path d="M0 250C120 240 230 262 330 280C220 272 110 270 0 288Z" fill="var(--orange)"/>
      <path d="M470 290C660 300 820 288 953 240V272C820 318 640 320 470 290Z" fill="var(--violet)"/>
    </svg>
    <div class="header-kicker">We Offering</div>
    <h1 class="header-title">BrivoMendup Program</h1>
  </header>

  <p class="intro">Our BrivoMendup program enables our clients to find solutions for financial situations that are keeping them from achieving their goal of ownership and living a fulfilled life. Our BrivoMendup program will help you settle your debt to the NTB, alleviate your credit burden with your creditors, and assist with some light bookkeeping that will make things easier during the tax season for small businesses and independent contractors. There is no reason to live a stressfull life when a solution is being offered to you. Our fees are reasonable and our service is fantastic. Our goal is to build a cliente base that will be happy with our service, and appreciate our company culture and at the same time become customers for life.</p>

  <div class="program-name">BrivoMendup</div>

  <div class="brand-box">
    <div class="brand-mark"></div>
    <div class="brand-name">Vel Marin Financing</div>
  </div>

  <div class="slogan">HAPPINESS,<br>RESTORED!</div>

  <div class="provide-tab">WE PROVIDE</div>
  <ul class="services">
    <li><svg viewBox="0 0 28 28" aria-hidden="true"><rect x="2" y="6" width="19" height="19" rx="3" fill="none" stroke="var(--navy)" stroke-width="2.5"/><path d="M7 15l5 5L26 3" fill="none" stroke="var(--orange)" stroke-width="4" stroke-linecap="round"/></svg>TAX PREPARATION</li>
    <li><svg viewBox="0 0 28 28" aria-hidden="true"><rect x="2" y="6" width="19" height="19" rx="3" fill="none" stroke="var(--navy)" stroke-width="2.5"/><path d="M7 15l5 5L26 3" fill="none" stroke="var(--orange)" stroke-width="4" stroke-linecap="round"/></svg>RESTORATION</li>
    <li><svg viewBox="0 0 28 28" aria-hidden="true"><rect x="2" y="6" width="19" height="19" rx="3" fill="none" stroke="var(--navy)" stroke-width="2.5"/><path d="M7 15l5 5L26 3" fill="none" stroke="var(--orange)" stroke-width="4" stroke-linecap="round"/></svg>CREDIT REPAIR</li>
    <li><svg viewBox="0 0 28 28" aria-hidden="true"><rect x="2" y="6" width="19" height="19" rx="3" fill="none" stroke="var(--navy)" stroke-width="2.5"/><path d="M7 15l5 5L26 3" fill="none" stroke="var(--orange)" stroke-width="4" stroke-linecap="round"/></svg>LEDGER PREPARATION</li>
    <li><svg viewBox="0 0 28 28" aria-hidden="true"><rect x="2" y="6" width="19" height="19" rx="3" fill="none" stroke="var(--navy)" stroke-width="2.5"/><path d="M7 15l5 5L26 3" fill="none" stroke="var(--orange)" stroke-width="4" stroke-linecap="round"/></svg>TAX RESTORATION</li>
  </ul>

  <div class="photo" role="img" aria-label="Photo of an open hand holding gold coins with a small green tree growing from them, beside a stack of silver coins"></div>

  <address class="address" style="font-style:normal">4870 Brookline Ave.<br>Dr. # C12, Dallas, TX 75201<br>E: info@velmarinfinancing.com</address>

  <p class="browse">Please feel free to browse our website for tools helpful to your needs.</p>

  <footer class="footer">
    <svg width="953" height="80" viewBox="0 0 953 80" aria-hidden="true">
      <rect x="0" y="0" width="953" height="80" fill="#ffffff"/>
      <path d="M0 6H580L540 80H0Z" fill="var(--navy)"/>
      <path d="M0 6H580L577 12H0Z" fill="#b8c6d6"/>
      <path d="M560 6H953V80H520Z" fill="var(--orange-deep)"/>
      <path d="M560 6H953V12H557Z" fill="#f7c06a"/>
    </svg>
    <div class="footer-web">www.velmarinfinancing.com</div>
    <div class="footer-call">CALL US: <strong>555.214.0387</strong></div>
  </footer>
</main>
</body>
</html>
```